Oil and Gas Exploration and Production company needs a business card design

We need a business card design using our logo and colors in the logo. We want a mainstream design.

```html
<!DOCTYPE html>
<html lang="en">
<head>
<meta charset="utf-8">
<title>Ardent Oil &amp; Gas — Business Card</title>
<link href="https://fonts.googleapis.com/css2?family=Open+Sans:wght@400;600;700&display=swap" rel="stylesheet">
<style>
  :root {
    --backdrop: #e6e6e4;
    --card: #ffffff;
    --ink: #1c1b1a;
    --panel: #2b2a29;
    --gold: #d4a12a;
    --muted: #6d6d6d;
    --on-panel: #ffffff;
  }
  * { box-sizing: border-box; margin: 0; padding: 0; }
  html, body {
    width: 1200px; height: 900px; overflow: hidden;
    background: var(--backdrop);
    font-family: "Open Sans", Arial, sans-serif;
  }
  .sheet {
    width: 1200px; height: 900px;
    display: flex; align-items: center; justify-content: center; gap: 40px;
  }
  .card {
    position: relative;
    width: 540px; height: 309px;
    background: var(--card);
    box-shadow: 0 2px 10px rgba(0,0,0,.12);
    overflow: hidden;
  }
  /* Front */
  .card-front {
    display: flex; flex-direction: column; align-items: center; justify-content: center;
  }
  .brand {
    display: flex; align-items: center; gap: 12px;
    margin-top: -20px;
  }
  .brand-dot {
    width: 22px; height: 22px; border-radius: 50%;
    background: var(--gold);
  }
  .brand-name {
    font-weight: 700; font-size: 38px; color: var(--ink);
    letter-spacing: .5px;
  }
  .website {
    position: absolute; bottom: 58px; left: 0; right: 0;
    text-align: center;
    font-size: 13px; letter-spacing: 6px; color: var(--muted);
  }
  /* Back */
  .drop-panel {
    position: absolute; left: 210px; top: 2px;
    width: 290px; height: 305px;
  }
  .drop-panel path { fill: var(--panel); stroke: var(--gold); stroke-width: 5; }
  .contact-block {
    position: absolute; left: 272px; top: 100px;
    color: var(--on-panel);
  }
  .person-name { font-weight: 700; font-size: 17px; letter-spacing: .5px; line-height: 1.2; }
  .person-title { font-size: 12px; letter-spacing: .5px; margin-bottom: 12px; }
  .address { font-size: 12.5px; line-height: 1.35; margin-bottom: 4px; }
  .contact-list { list-style: none; font-size: 12.5px; line-height: 1.45; }
  .contact-list li { display: flex; align-items: center; gap: 6px; }
  .contact-list svg { width: 12px; height: 12px; fill: var(--on-panel); flex: none; }
</style>
</head>
<body>
<main class="sheet">
  <section class="card card-front" aria-label="Card front">
    <div class="brand">
      <span class="brand-dot"></span>
      <span class="brand-name">Ardent Oil &amp; Gas</span>
    </div>
    <p class="website">www.ardentoilgas.com</p>
  </section>

  <section class="card card-back" aria-label="Card back">
    <svg class="drop-panel" viewBox="0 0 290 305" aria-hidden="true">
      <path d="M145 6 C172 62 282 100 282 166 A137 137 0 0 1 8 166 C8 100 118 62 145 6 Z"/>
    </svg>
    <div class="contact-block">
      <p class="person-name">MARK ELLISON</p>
      <p class="person-title">PRESIDENT</p>
      <p class="address">4127 Harbor Ridge Road<br>Millbrook, NY 12545</p>
      <ul class="contact-list">
        <li><svg viewBox="0 0 12 12" aria-hidden="true"><path d="M2 1h2.5l1 3-1.5 1a6 6 0 0 0 3 3l1-1.5 3 1V10a1 1 0 0 1-1 1A10 10 0 0 1 1 2a1 1 0 0 1 1-1z"/></svg>555 0142 7781</li>
        <li><svg viewBox="0 0 12 12" aria-hidden="true"><path d="M3 0h6a1 1 0 0 1 1 1v10a1 1 0 0 1-1 1H3a1 1 0 0 1-1-1V1a1 1 0 0 1 1-1zm0 2v7h6V2z"/></svg>555 0196 3324</li>
        <li><svg viewBox="0 0 12 12" aria-hidden="true"><path d="M3 0h6v3H3zM1 4h10a1 1 0 0 1 1 1v5H0V5a1 1 0 0 1 1-1zm2 3v1h6V7z"/></svg>555 0173 5508</li>
        <li><svg viewBox="0 0 12 12" aria-hidden="true"><path d="M0 2h12v1L6 7 0 3zm0 2.5 6 4 6-4V10H0z"/></svg>info@ardentoilgas.com</li>
      </ul>
    </div>
  </section>
</main>
</body>
</html>
```